TEBSIRK HOA Portal Site for Public

Clean up and organize current website; need website to look good and functional; this is a HOA (homeowner association management) website where homeowners can login and pay their bill, general information about a HOA, monthly newsletter page.
Competitors:
https://quillmarsh.example/
https://dorvinpalms.example/
https://www.kelbrookhomes.example/nevada
http://www.tpw-hoa.example/

Target Market(s)

homeowners

Industry/Entity Type

Real Estate

Coding

Coded - Design and coding required

Number of Pages Required

5+ page

Font styles to use
Serif

Colors
0292cd
33a6d7
e667a6
e34297

Requirements
Must have
• login to pay
• services page
• contact us
• order resale package
Nice to have
• page why an HOA would contract us

```html
<!DOCTYPE html>
<html lang="en">
<head>
<meta charset="utf-8">
<title>TEBSIRK HOA</title>
<link href="https://fonts.googleapis.com/css2?family=Libre+Baskerville:wght@700&family=Montserrat:wght@500;600&family=Mulish:wght@400;600;700&display=swap" rel="stylesheet">
<style>
:root{
  --blue:#0292cd;
  --blue-light:#33a6d7;
  --blue-deep:#0a73a8;
  --pink:#e667a6;
  --pink-deep:#e34297;
  --ink:#333;
  --muted:#8a8a8a;
  --soft:#f5f5f5;
  --dark:#2b2b2b;
  --line:#dcdcdc;
}
*{margin:0;padding:0;box-sizing:border-box}
html,body{width:1200px;height:3526px;overflow:hidden}
body{position:relative;font-family:"Mulish",sans-serif;color:var(--ink);background:#fff}
.abs{position:absolute}
.center{left:0;width:1200px;text-align:center}
.head{font-family:"Montserrat",sans-serif;font-weight:600}
.btn{position:absolute;display:flex;align-items:center;justify-content:center;color:#fff;font-size:15px;font-weight:600;text-transform:uppercase;letter-spacing:.3px;background:linear-gradient(var(--pink),var(--pink-deep))}
.blue-band{background:linear-gradient(var(--blue-light),var(--blue-deep))}

.topbar{top:0;left:0;width:1200px;height:52px}
.topbar .info{top:15px;color:#fff;font-size:15px;font-weight:600;display:flex;align-items:center;gap:10px}
.logo{top:72px;font-family:"Libre Baskerville",serif;font-size:46px;color:var(--blue);letter-spacing:1px}
.nav{top:148px;left:0;width:1200px;font-size:15px;color:#7a7a7a;text-transform:uppercase}
.nav span{position:absolute}
.nav .active{color:var(--pink-deep)}

.hero{top:198px;left:0;width:1200px;height:572px;background:linear-gradient(135deg,#5e5650,#8a7c70 45%,#4a423d)}
.hero h1{top:140px;font-family:"Montserrat",sans-serif;font-weight:600;font-size:50px;line-height:63px;color:#fff;text-transform:uppercase}
.hero p{top:280px;left:180px;width:840px;text-align:center;font-weight:700;font-size:17px;line-height:28px;color:#fff}
.arrow{width:52px;height:52px;border-radius:50%;top:259px}

.offer{top:770px;left:0;width:1200px;height:562px;color:#fff}
.offer h2{top:60px;font-size:46px}
.offer p{position:absolute;left:260px;width:680px;text-align:center;font-size:14.5px;line-height:23px}

.feature{top:1332px;width:500px}
.feature h3{position:absolute;top:205px;font-size:30px;line-height:33px;color:var(--ink)}
.feature p{position:absolute;top:287px;font-size:14.5px;line-height:26px;color:var(--muted)}
.feature .icon{position:absolute;top:60px;left:-2px;width:116px;height:116px;border-radius:50%;background:#fff;box-shadow:0 4px 12px rgba(0,0,0,.18)}

.feedback{top:1792px;left:0;width:1200px;height:561px;background:var(--soft)}
.feedback h2{top:60px;font-size:46px}
.card{top:144px;width:313px;height:353px;background:#fff;border:1px solid #e6e6e6;text-align:center}
.card.featured{background:linear-gradient(var(--pink),var(--pink-deep));color:#fff;border:none}
.card .avatar{position:absolute;left:104px;top:34px;width:104px;height:104px;border-radius:50%;border:4px solid var(--pink);background:linear-gradient(#d9e6f0,#9fb7c9)}
.card.featured .avatar{border-color:var(--blue-light)}
.card .stars{position:absolute;left:0;width:100%;top:161px}
.card p{position:absolute;left:20px;width:273px;top:198px;font-size:14.5px;line-height:26px;color:var(--muted)}
.card.featured p{color:#fff}
.card .name{position:absolute;left:0;width:100%;top:288px;font-size:18px;font-weight:600;color:var(--ink)}
.card.featured .name{color:#fff}

.proposal{top:2353px;left:0;width:1200px;height:249px;color:#fff}
.proposal h2{top:56px;font-size:50px}

.contact h2{top:2660px;font-size:46px;color:var(--ink)}
.contact .sub{top:2736px;font-size:14.5px;color:var(--muted)}
.field{position:absolute;border:1px solid var(--line);border-radius:3px;font-size:14.5px;color:#777;padding:22px 17px}

.footer{top:3112px;left:0;width:1200px;height:312px;background:var(--dark);color:#fff}
.footer .brand{position:absolute;left:79px;top:60px;font-size:30px}
.footer .addr{position:absolute;left:79px;top:112px;font-size:17px;line-height:29px}
.footer .line{position:absolute;left:79px;font-size:17px}
.footer .line b{display:inline-block;width:72px}
.news{position:absolute;left:581px;top:63px;width:541px;height:170px;border:3px solid var(--blue)}
.news h4{position:absolute;left:28px;top:30px;font-family:"Montserrat",sans-serif;font-weight:500;font-size:23px}
.news .input{position:absolute;left:26px;top:77px;width:312px;height:56px;background:#fff;color:#777;font-size:14px;padding:19px 13px}
.news .sub-btn{position:absolute;left:348px;top:77px;width:162px;height:56px;border:2px solid #fff;display:flex;align-items:center;justify-content:center;font-size:15px;font-weight:700}

.copy{top:3465px;left:79px;font-size:13.5px;color:var(--muted)}
.copy b{color:#444;font-weight:700}
.social{top:3456px;width:37px;height:37px;border-radius:2px}
</style>
</head>
<body>

<header>
  <div class="abs topbar blue-band"></div>
  <div class="abs topbar"><!-- contact details -->
    <div class="abs info" style="left:77px">
      <svg width="20" height="20" viewBox="0 0 24 24" fill="none" stroke="#fff" stroke-width="1.6"><path d="M5 3h4l2 5-3 2a12 12 0 0 0 6 6l2-3 5 2v4a2 2 0 0 1-2 2A18 18 0 0 1 3 5a2 2 0 0 1 2-2z"/></svg>
      123.456.7890
    </div>
    <div class="abs info" style="left:246px">
      <svg width="20" height="16" viewBox="0 0 24 18" fill="none" stroke="#fff" stroke-width="1.6"><rect x="1" y="1" width="22" height="16"/><path d="M1 1l11 9 11-9"/></svg>
      info@tebsirkhoa.example
    </div>
  </div>
  <div class="btn" style="left:925px;top:0;width:197px;height:62px;border-radius:0 0 3px 3px">Contact Us</div>
  <div class="abs center logo">TEBSIRK HOA</div>
  <nav class="abs nav">
    <span class="active" style="left:182px">Home</span>
    <span style="left:276px">Services</span>
    <span style="left:380px">Why an HOA would contract us</span>
    <span style="left:687px">Order resale package</span>
    <span style="left:921px">Contact us</span>
  </nav>
</header>

<section class="abs hero" role="img" aria-label="Photo of a family relaxing together in a living room">
  <h1 class="abs center">Homeowner Association<br>Management</h1>
  <p class="abs">Lorem ipsum dolor sit amet, consectetur adipiscing elit, sed do eiusmod tempor incididunt ut labore et dolore magna aliqua. Ut enim ad minim veniam, quis nostrud exercitation.</p>
  <div class="btn" style="left:495px;top:370px;width:208px;height:50px;border-radius:3px">Login to Pay</div>
  <div class="abs arrow" style="left:51px;background:var(--blue-deep)">
    <svg width="52" height="52" viewBox="0 0 52 52" fill="none" stroke="#fff" stroke-width="2.5"><path d="M29 20l-6 6 6 6"/></svg>
  </div>
  <div class="abs arrow" style="left:1096px;background:rgba(255,255,255,.35)">
    <svg width="52" height="52" viewBox="0 0 52 52" fill="none" stroke="#333" stroke-width="2"><path d="M23 20l6 6-6 6"/></svg>
  </div>
</section>

<section class="abs offer blue-band">
  <h2 class="abs center head">What We Offer</h2>
  <p style="top:133px">Accessible, licensed Association Managers</p>
  <p style="top:169px">24 hour Web site access: online account information</p>
  <p style="top:205px">24 hour emergency service</p>
  <p style="top:242px">Provide monthly financial reports to the Board of Directors</p>
  <p style="top:278px">Read, study and understand all governing documents of the Association. Correspond with members in violation of the CC&amp;Rs, By-laws, Rules &amp; Regulations and report the status of all noncompliance to the Board of Directors in a timely manner.</p>
  <p style="top:361px;left:310px;width:580px">Act as the custodian of the corporate records. Coordinate preparing annual tax returns for the Association.</p>
  <div class="btn" style="left:527px;top:448px;width:145px;height:52px;border-radius:3px">Read More</div>
</section>

<section>
  <div class="abs feature" style="left:79px">
    <div class="icon" role="img" aria-label="Line icon of a house"></div>
    <h3 class="head">Association Management<br>Services</h3>
    <p>Lorem ipsum dolor sit amet, consectetur adipiscing elit, sed do thereof eiusmod tempor incididunt ut labore et dolore magna aliqua. Ut enim ad minim veniam, quis nostrud exercitation ullamco there laboris nisi ut aliquip ex ea commodo consequat.</p>
  </div>
  <div class="abs feature" style="left:635px">
    <div class="icon" role="img" aria-label="Line icon of a manager with a gear"></div>
    <h3 class="head">TEBSIRK manages communities<br>throughout Southern Nevada</h3>
    <p>Lorem ipsum dolor sit amet, consectetur adipiscing elit, sed do thereo eiusmod tempor incididunt ut labore et dolore magna aliqua. Ut enim ad minim veniam, quis nostrud exercitation ullamco there laboris nisi ut aliquip ex ea commodo consequat.</p>
  </div>
</section>

<svg width="0" height="0" style="position:absolute">
  <defs>
    <symbol id="star" viewBox="0 0 20 20"><path d="M10 1l2.6 6 6.4.5-4.9 4.2 1.5 6.3L10 14.6 4.4 18l1.5-6.3L1 7.5 7.4 7z"/></symbol>
  </defs>
</svg>

<section class="abs feedback">
  <h2 class="abs center head">Clients Feedback</h2>
  <div class="abs card" style="left:77px">
    <div class="avatar" role="img" aria-label="Client portrait"></div>
    <div class="stars"><svg width="84" height="17" viewBox="0 0 100 20"><g fill="#f0b400" stroke="#b88a00"><use href="#star" x="0" width="20"/><use href="#star" x="20" width="20"/><use href="#star" x="40" width="20"/><use href="#star" x="60" width="20"/></g><use href="#star" x="80" width="20" fill="none" stroke="#999"/></svg></div>
    <p>Lorem ipsum dolor amet, consectetur adipiscing elit, sed do thereof eiusmod tempor incididunt ut labore.</p>
    <div class="name head">- Client Name</div>
  </div>
  <div class="abs card featured" style="left:443px">
    <div class="avatar" role="img" aria-label="Client portrait"></div>
    <div class="stars"><svg width="84" height="17" viewBox="0 0 100 20"><g fill="#fff" stroke="#fff"><use href="#star" x="0" width="20"/><use href="#star" x="20" width="20"/><use href="#star" x="40" width="20"/><use href="#star" x="60" width="20"/></g><use href="#star" x="80" width="20" fill="none" stroke="#fff"/></svg></div>
    <p>Lorem ipsum dolor amet, consectetur adipiscing elit, sed do thereof eiusmod tempor incididunt ut labore.</p>
    <div class="name head">- Client Name</div>
  </div>
  <div class="abs card" style="left:810px">
    <div class="avatar" role="img" aria-label="Client portrait"></div>
    <div class="stars"><svg width="84" height="17" viewBox="0 0 100 20"><g fill="#f0b400" stroke="#b88a00"><use href="#star" x="0" width="20"/><use href="#star" x="20" width="20"/><use href="#star" x="40" width="20"/><use href="#star" x="60" width="20"/></g><use href="#star" x="80" width="20" fill="none" stroke="#999"/></svg></div>
    <p>Lorem ipsum dolor amet, consectetur adipiscing elit, sed do thereof eiusmod tempor incididunt ut labore.</p>
    <div class="name head">- Client Name</div>
  </div>
</section>

<section class="abs proposal blue-band">
  <h2 class="abs center head">Request a Free Proposal Now!</h2>
  <div class="btn" style="left:495px;top:135px;width:208px;height:51px;border-radius:3px">Request Proposal</div>
</section>

<section class="contact">
  <h2 class="abs center head">Contact Us</h2>
  <div class="abs center sub">Drop us a line to ask a question or to request a proposal click the button above.</div>
  <div class="field" style="left:230px;top:2800px;width:239px;height:62px">Name :</div>
  <div class="field" style="left:480px;top:2800px;width:239px;height:62px">Email &nbsp;:</div>
  <div class="field" style="left:730px;top:2800px;width:239px;height:62px">Phone :</div>
  <div class="field" style="left:230px;top:2873px;width:739px;height:113px;padding-top:14px">Message / Comments :</div>
  <div class="btn" style="left:495px;top:2999px;width:208px;height:50px;border-radius:3px">Submit Now</div>
</section>

<footer class="abs footer">
  <div class="brand head">TEBSIRK HOA</div>
  <div class="addr">123, Address, State Name,<br>City Name,Zipcode</div>
  <div class="line" style="top:192px"><b>Phone :</b>123.456.7890</div>
  <div class="line" style="top:223px"><b>Email :</b>info@tebsirkhoa.example</div>
  <div class="news">
    <h4>Receive important information &amp; updates</h4>
    <div class="input">Enter Email Address...</div>
    <div class="sub-btn">SUBSCRIBE NOW</div>
  </div>
</footer>

<div class="abs copy">Copyright © <b>TEBSIRK HOA</b> - 2019 . All Right Reserved</div>
<div class="abs social" style="left:945px;background:#3b5998" aria-label="Social link 1"></div>
<div class="abs social" style="left:992px;background:#1da1f2" aria-label="Social link 2"></div>
<div class="abs social" style="left:1038px;background:#c8432b" aria-label="Social link 3"></div>
<div class="abs social" style="left:1086px;background:#0a73a8" aria-label="Social link 4"></div>

</body>
</html>
```